Tour Guide in Israel business card

I am a tour guide in Israel (the holy land). Prior to it I have over 20 years high-tech business. My main (but not only) focus is working with business people that come to Israel and want to get a tour (usually short from few hours to 2 days). During my guiding I incorporate a lot of my know how of the Israeli business culture. I like to have a business card that I can present to anyone that is looking for a tour guide, but that business people will understand the additional value I can provide them during my tour.

Target Market(s)

Business visitors and tourist to Israel

Industry/Entity Type

Tourism

Contact Information for Business Card

Danny Korvath
email: danny@korvath-tours.example
Mobile: +972-52-7416205

Colors

Designer to choose colors to be used in the design.

Requirements
Must have
• Tour Guide
Nice to have
• I don't know how but it should project my understanding in business not just the tourist side of my knowledge.

```html
<!DOCTYPE html>
<html lang="en">
<head>
<meta charset="utf-8">
<title>Danny Korvath – Business Card</title>
<link href="https://fonts.googleapis.com/css2?family=Roboto+Condensed:wght@300;400;700&family=Roboto:wght@400&display=swap" rel="stylesheet">
<style>
  :root {
    --backdrop: #e4e4e4;
    --card-light: #f4f4f4;
    --accent-bar: #c2c2c2;
    --navy: #0f3a5c;
    --ink: #4a4a4a;
    --deep-top: #0f5f8c;
    --deep-bottom: #06192a;
    --label: #5f7b91;
    --glow: #4cc6f2;
  }
  * { margin: 0; padding: 0; box-sizing: border-box; }
  html, body { width: 1200px; height: 1047px; overflow: hidden; }
  body { background: var(--backdrop); position: relative; }

  .card {
    position: absolute;
    top: 253px;
    width: 302px;
    height: 541px;
    box-shadow: 0 2px 4px rgba(0,0,0,0.18);
  }

  /* Front */
  .card-front { left: 269px; background: var(--card-light); }
  .accent-bar {
    position: absolute; left: 0; top: 250px; bottom: 0; width: 26px;
    background: var(--accent-bar);
  }
  .identity { position: absolute; left: 54px; top: 246px; }
  .first-name, .last-name {
    font-family: "Roboto Condensed", sans-serif;
    color: var(--navy);
    font-size: 44px;
    line-height: 40px;
    letter-spacing: -0.5px;
  }
  .first-name { font-weight: 300; }
  .last-name { font-weight: 700; }
  .role {
    margin-top: 10px;
    font-family: "Roboto Condensed", sans-serif;
    font-weight: 300;
    font-size: 19px;
    color: var(--ink);
  }
  .contacts {
    position: absolute; left: 54px; top: 414px;
    list-style: none;
    font-family: "Roboto Condensed", sans-serif;
    font-weight: 300;
    font-size: 18px;
    line-height: 28px;
    color: var(--ink);
  }

  /* Back */
  .card-back {
    left: 630px;
    background: linear-gradient(180deg, var(--deep-top) 0%, #0b3f62 50%, var(--deep-bottom) 100%);
    overflow: hidden;
  }
  .network-map {
    position: absolute; left: 88px; top: 70px; width: 130px; height: 332px;
    border-radius: 45% 55% 40% 50% / 20% 25% 50% 45%;
    background: radial-gradient(ellipse at 50% 40%, rgba(76,198,242,0.45) 0%, rgba(40,140,200,0.25) 55%, rgba(15,95,140,0) 80%);
  }
  .theme-label {
    position: absolute;
    font-family: "Roboto Condensed", sans-serif;
    font-weight: 300;
    font-size: 17px;
    color: var(--label);
    transform-origin: center;
    white-space: nowrap;
  }
  .label-land { left: 151px; top: 70px; transform: translate(-50%,-50%) rotate(-12deg); }
  .label-history { left: 206px; top: 171px; transform: translate(-50%,-50%) rotate(78deg); }
  .label-business { left: 198px; top: 271px; transform: translate(-50%,-50%) rotate(88deg); }
  .label-people { left: 92px; top: 187px; transform: translate(-50%,-50%) rotate(-68deg); }
  .label-culture { left: 74px; top: 303px; transform: translate(-50%,-50%) rotate(-82deg); }
  .label-faith { left: 99px; top: 375px; transform: translate(-50%,-50%) rotate(-82deg); }
  .tagline {
    position: absolute; left: 0; right: 0; top: 469px;
    text-align: center;
    font-family: "Roboto", sans-serif;
    font-size: 17px;
    letter-spacing: 1.2px;
    color: var(--glow);
  }
</style>
</head>
<body>
  <section class="card card-front">
    <div class="accent-bar"></div>
    <div class="identity">
      <div class="first-name">DANNY</div>
      <div class="last-name">KORVATH</div>
      <div class="role">Tour Leader &amp; Storyteller</div>
    </div>
    <ul class="contacts">
      <li>+972-52-7416205</li>
      <li>danny@korvath-tours.example</li>
      <li>www.korvath-tours.example</li>
    </ul>
  </section>

  <section class="card card-back">
    <div class="network-map" role="img" aria-label="Map of Israel drawn as a glowing network of connected dots"></div>
    <span class="theme-label label-land">Land</span>
    <span class="theme-label label-history">History</span>
    <span class="theme-label label-business">Business</span>
    <span class="theme-label label-people">People</span>
    <span class="theme-label label-culture">Culture</span>
    <span class="theme-label label-faith">Faith</span>
    <div class="tagline">CONNECTING THE DOTS</div>
  </section>
</body>
</html>
```